Modern Banner for use on Emails and Electronic letters.

We need a Email banner that we can also uses as a banner on electronic documents . Would be a bonus to be able to use banner on facebook.
The banner should incorporate our logo and company name; The Calvora Group.
We would like an eye catching, modern design.
We are completely open to using colour and/or images along with our logo and company name.
Currently the font for our company name is time new roman but again we are open to suggestions. The company name can be be moved away from the umbrella logo to anywhere in the banner.

Industry/Entity Type

Electronic

Font styles to use
Serif
Sans Serif

Colors

Designer to choose colors to be used in the design.

Requirements
Must have
• Calvora Logo (Umbrella design - Black umbrella on red blocks with a letter on each block spelling VORA.
• Company name: The Calvora Group
• Be Modern and professional.
• Suitable for use as an email banner but can also be used as letterhead on electronic documents.
Nice to have
• Colour and/or images.
• Be able to be used as facebook banner.

```html
<!DOCTYPE html>
<html lang="en">
<head>
<meta charset="utf-8">
<title>The Calvora Group — Letterhead</title>
<link rel="stylesheet" href="https://fonts.googleapis.com/css2?family=Tinos&display=swap">
<style>
  :root {
    --paper: #ffffff;
    --ink: #111111;
    --red: #e8140f;
    --red-deep: #8a0a06;
    --rule-dark: #1a1a1a;
    --rule-light: #9aa3a3;
  }
  html, body {
    margin: 0;
    padding: 0;
    overflow: hidden;
    background: var(--paper);
  }
  .letterhead {
    position: relative;
    width: 873px;
    height: 1200px;
    background: var(--paper);
    overflow: hidden;
    font-family: "Tinos", "Times New Roman", serif;
  }
  .block-cluster {
    position: absolute;
    top: 0;
    width: 81px;
    height: 111px;
    background: linear-gradient(135deg, var(--red) 0%, #c10f0a 55%, var(--red-deep) 100%);
  }
  .block-cluster--left { left: 0; }
  .block-cluster--right { right: 0; }
  .brand-mark {
    position: absolute;
    left: 128px;
    top: 40px;
    width: 118px;
    text-align: center;
    font-size: 26px;
    line-height: 1;
    color: var(--ink);
  }
  .wordmark {
    position: absolute;
    left: 330px;
    top: 40px;
    margin: 0;
    font-weight: 400;
    color: var(--ink);
    white-space: nowrap;
    line-height: 1;
  }
  .wordmark__small { font-size: 29px; }
  .wordmark__main { font-size: 48px; }
  .header-rule {
    position: absolute;
    left: 0;
    top: 118px;
    width: 873px;
    height: 5px;
    background: linear-gradient(90deg,
      var(--rule-dark) 0%, var(--rule-dark) 25%,
      var(--rule-light) 38%, var(--rule-dark) 50%,
      var(--rule-dark) 60%, var(--rule-light) 70%,
      var(--rule-dark) 82%, var(--rule-dark) 100%);
  }
  .cubes {
    position: absolute;
    left: 0;
    top: 0;
  }
  .cube { fill: var(--red); }
  .cube-shade { fill: var(--red-deep); }
</style>
</head>
<body>
  <div class="letterhead">
    <div class="block-cluster block-cluster--left" role="img" aria-label="Stacked red 3D blocks"></div>
    <div class="block-cluster block-cluster--right" role="img" aria-label="Stacked red 3D blocks"></div>

    <div class="brand-mark">Calvora</div>

    <h1 class="wordmark">
      <span class="wordmark__small">The</span>
      <span class="wordmark__main">Calvora</span>
      <span class="wordmark__small">Group</span>
    </h1>

    <svg class="cubes" width="873" height="1200" viewBox="0 0 873 1200" aria-hidden="true">
      <g>
        <rect class="cube" x="302" y="15" width="8" height="8"/>
        <rect class="cube" x="85" y="38" width="8" height="8"/>
        <rect class="cube" x="292" y="53" width="9" height="9"/>
        <rect class="cube" x="226" y="73" width="12" height="11"/>
        <rect class="cube" x="130" y="94" width="12" height="11"/>
        <rect class="cube" x="262" y="87" width="15" height="14"/>
        <rect class="cube" x="668" y="78" width="12" height="11"/>
        <rect class="cube" x="733" y="6" width="11" height="10"/>
        <rect class="cube" x="703" y="41" width="10" height="9"/>
        <rect class="cube" x="761" y="41" width="10" height="9"/>
        <rect class="cube" x="740" y="86" width="8" height="8"/>
        <rect class="cube" x="796" y="2" width="8" height="8"/>
        <rect class="cube" x="818" y="1173" width="34" height="27"/>
        <rect class="cube-shade" x="840" y="1173" width="12" height="27"/>
      </g>
    </svg>

    <div class="header-rule"></div>
  </div>
</body>
</html>
```